BRINDLEWOOD EXTRA VIRGIN OLIVE OIL

I needs a design for an Australian Extra Virgin Olive Oil.

The label will go on a round clear bottle

The label size front and back is 145mm high x 60mm wide.

The important points for the design are as follows.

I want to see elegant olives on the label so that non English speaking markets can easily understand its olive oil. I want it too look classy . IT must also look Australian but I don't want to see kangaroos just colours that reflect Australia.

The mandatory info on front label will be

BRINDLEWOOD

Cold Pressed
EXTRA VIRGIN OLIVE OIL

AUSTRALIAN

1 litre

```html
<!DOCTYPE html>
<html lang="en">
<head>
<meta charset="utf-8">
<title>BRINDLEWOOD | Extra Virgin Oil Label - 145x60 mm</title>
<link rel="stylesheet" href="https://fonts.googleapis.com/css2?family=Fira+Sans:wght@200;300;400&display=swap">
<style>
  :root {
    --sheet: #ffffff;
    --rule: #8a8a8a;
    --ink: #2b2b2b;
    --dim: #c8c8c8;
    --dim-text: #a8a8a8;
    --olive: #4a4000;
    --cream: #f0ede8;
    --cream-text: #f3efe2;
    --dark-text: #3a3a3a;
    --tag: #3b2414;
  }
  * { box-sizing: border-box; margin: 0; padding: 0; }
  html, body { width: 1200px; height: 848px; overflow: hidden; background: var(--sheet); }
  body { position: relative; font-family: "Fira Sans", sans-serif; font-weight: 300; color: var(--ink); }

  .sheet-rule { position: absolute; left: 57px; width: 1086px; height: 1px; background: var(--rule); }
  .sheet-rule.top { top: 31px; }
  .sheet-rule.mid { top: 52px; }
  .sheet-rule.bottom { top: 811px; }
  .sheet-title, .sheet-date {
    position: absolute; top: 34px; font-size: 13px; line-height: 16px; letter-spacing: 1.2px; font-weight: 300; color: var(--ink);
  }
  .sheet-title { left: 58px; }
  .sheet-date { right: 57px; }

  .dimension { position: absolute; }
  .dimension svg { display: block; }
  .dimension-width { top: 112px; width: 240px; }
  .dimension-width .value { position: absolute; top: 0; left: 0; width: 100%; text-align: center; font-size: 10px; color: var(--dim-text); }
  .dimension-width svg { margin-top: 12px; }
  .dimension-height { top: 161px; width: 20px; }
  .dimension-height .value {
    position: absolute; top: 282px; left: -6px; font-size: 10px; color: var(--dim-text); transform: rotate(-90deg);
  }

  .label {
    position: absolute; top: 161px; width: 240px; height: 582px; text-align: center;
  }
  .label--olive { left: 99px; background: var(--olive); color: var(--cream-text); }
  .label--cream { left: 701px; background: var(--cream); color: var(--dark-text); }

  .brand-mark {
    position: absolute; top: 56px; left: 60px; width: 120px; height: 120px; border-radius: 50%;
    display: flex; align-items: center; justify-content: center;
    font-size: 14px; letter-spacing: 1.5px; font-weight: 400;
  }
  .label--olive .brand-mark { background: var(--cream-text); color: var(--olive); }
  .label--cream .brand-mark { background: var(--olive); color: var(--cream-text); }

  .label-line { position: absolute; left: 0; width: 100%; line-height: 1.2; }
  .process { top: 253px; font-size: 11px; }
  .grade { top: 270px; font-size: 16px; }
  .product { top: 290px; font-size: 42px; font-weight: 200; letter-spacing: 0.5px; }
  .origin { top: 533px; font-size: 17px; }
  .volume { top: 562px; font-size: 11px; }

  .label-tag {
    position: absolute; top: 778px; height: 16px; padding: 0 6px; border-radius: 4px;
    background: var(--tag); color: #fff; font-size: 9px; font-weight: 400; line-height: 16px;
  }
</style>
</head>
<body>
  <div class="sheet-rule top"></div>
  <div class="sheet-title">BRINDLEWOOD &nbsp;|&nbsp; EXTRA VIRGIN OIL LABEL - 145x60 mm</div>
  <div class="sheet-date">27.FEB.2013</div>
  <div class="sheet-rule mid"></div>

  <div class="dimension dimension-width" style="left:99px">
    <span class="value">60</span>
    <svg width="240" height="28"><path d="M0.5 0V28M239.5 0V28M0 6H240" stroke="#c8c8c8" fill="none"/></svg>
  </div>
  <div class="dimension dimension-height" style="left:58px">
    <svg width="20" height="582"><path d="M0 0.5H20M0 581.5H20M6 0V582" stroke="#c8c8c8" fill="none"/></svg>
    <span class="value">145</span>
  </div>
  <section class="label label--olive">
    <div class="brand-mark">BRINDLEWOOD</div>
    <p class="label-line process">Cold Pressed</p>
    <p class="label-line grade">Extra virgin</p>
    <p class="label-line product">Olive Oil</p>
    <p class="label-line origin">Australian</p>
    <p class="label-line volume">1 litre</p>
  </section>
  <span class="label-tag" style="left:199px">Label 13</span>

  <div class="dimension dimension-width" style="left:701px">
    <span class="value">60</span>
    <svg width="240" height="28"><path d="M0.5 0V28M239.5 0V28M0 6H240" stroke="#c8c8c8" fill="none"/></svg>
  </div>
  <div class="dimension dimension-height" style="left:660px">
    <svg width="20" height="582"><path d="M0 0.5H20M0 581.5H20M6 0V582" stroke="#c8c8c8" fill="none"/></svg>
    <span class="value">145</span>
  </div>
  <section class="label label--cream">
    <div class="brand-mark">BRINDLEWOOD</div>
    <p class="label-line process">Cold Pressed</p>
    <p class="label-line grade">Extra virgin</p>
    <p class="label-line product">Olive Oil</p>
    <p class="label-line origin">Australian</p>
    <p class="label-line volume">1 litre</p>
  </section>
  <span class="label-tag" style="left:801px">Label 14</span>

  <div class="sheet-rule bottom"></div>
</body>
</html>
```